New Business Card Design Project LORVANTI-Italy

we are LORVANTI-Italy
our company in the market for 3 years we are luxury cosmetic company and its about time for a facelift :)
i will like to have elegant luxurious and unique business card
that will give the person that get it a unique, luxurious and elegant impression
I'm VERY OPEN FOR NEW IDEAS , even duo i add a few files of things that i see on line and i like them

i add my logo as well
my website is LORVANTI.COM
(if you would like to see the main style that we have)

Target Market(s)

adult that have money :)

Industry/Entity Type

Business

Contact Information for Business Card

Name - Dario Lorvanti
Position - CEO and CO Founder
address - 4817 E Halvern
telephone - 555-384-1926
email - dario@lorvanti.com
fax - 555-384-1926
website - LORVANTI.COM

Colors
000000
959595
fbee3e
ffffff

Requirements
Must have
• big logo in GOLD color
• elegant look
• impressive
Nice to have
• not must but maybe classy pattern background
• not must but maybe emblem
• maybe clear plastic business card
Should not have
• colors
• images

```html
<!DOCTYPE html>
<html lang="en">
<head>
<meta charset="utf-8">
<title>LORVANTI-Italy Business Card</title>
<link rel="stylesheet" href="https://fonts.googleapis.com/css2?family=Cinzel:wght@400;600&family=Source+Sans+3:wght@400&display=swap">
<style>
  :root {
    --backdrop: #3d3430;
    --card-black: #0e0e0f;
    --card-edge: #1c1c1e;
    --silver: #c9c9c9;
    --gold: #d9ad3c;
    --gold-soft: #c99a2e;
  }
  * { margin: 0; padding: 0; box-sizing: border-box; }
  html, body {
    width: 1200px;
    height: 864px;
    overflow: hidden;
    background: var(--backdrop);
  }
  .canvas {
    position: relative;
    width: 1200px;
    height: 864px;
  }
  .card {
    position: absolute;
    width: 540px;
    height: 310px;
    background: var(--card-black);
    border: 1px solid var(--card-edge);
    box-shadow: 0 14px 30px rgba(0,0,0,0.45);
  }
  .card--front { left: 80px; top: 90px; }
  .card--back  { left: 580px; top: 460px; }

  .brand {
    position: absolute;
    display: flex;
    flex-direction: column;
    align-items: center;
    gap: 16px;
  }
  .brand__mark {
    width: 58px;
    height: 58px;
    border-radius: 50%;
    border: 2px solid currentColor;
  }
  .brand__name {
    font-family: "Cinzel", serif;
    font-weight: 600;
    font-size: 34px;
    letter-spacing: 1px;
  }
  .card--front .brand {
    color: var(--silver);
    left: 0; right: 0; top: 86px;
  }
  .card--back .brand {
    color: var(--gold);
    left: 20px; width: 230px; top: 88px;
  }
  .card--back .brand__name { font-size: 30px; }

  .divider {
    position: absolute;
    left: 270px;
    top: 40px;
    width: 1px;
    height: 230px;
    background: var(--gold-soft);
  }
  .contact {
    position: absolute;
    left: 294px;
    top: 56px;
    color: var(--gold);
    font-family: "Source Sans 3", sans-serif;
    font-size: 13px;
    line-height: 1.45;
  }
  .contact__name {
    font-family: "Cinzel", serif;
    font-weight: 600;
    font-size: 19px;
    letter-spacing: 0.5px;
    line-height: 1.1;
  }
  .contact__role { font-size: 14px; margin-bottom: 14px; }
  .contact__address { margin-bottom: 8px; }
  .contact__web { margin-top: 14px; font-size: 14px; }
</style>
</head>
<body>
<main class="canvas">
  <section class="card card--front" aria-label="Business card front">
    <div class="brand">
      <span class="brand__mark"></span>
      <span class="brand__name">LORVANTI</span>
    </div>
  </section>

  <section class="card card--back" aria-label="Business card back">
    <div class="brand">
      <span class="brand__mark"></span>
      <span class="brand__name">LORVANTI</span>
    </div>
    <span class="divider"></span>
    <div class="contact">
      <p class="contact__name">Dario Lorvanti</p>
      <p class="contact__role">CEO &amp; CO Founder</p>
      <p class="contact__address">4817 E Halvern</p>
      <p>P : 555-384-1926</p>
      <p>F : 555-384-1926</p>
      <p>E : dario@lorvanti.com</p>
      <p class="contact__web">WWW.LORVANTI.COM</p>
    </div>
  </section>
</main>
</body>
</html>
```